Site re-branding and modernization

Two Managed Service Providers (Information Technology) have merged and need an update to their website. The site needs to be re-branded from "Ridgeline Computing" with a blue theme to "Harbor Systems" with an orange theme.

Harbor Systems provides small and medium business with an outsourced IT department, offering enterprise level IT to business that otherwise wouldn't have it. Our marketing has been centered around a row of apples with one orange and a caption that says, "We do IT our own way and we're happy about it!" Hence the orange color scheme needed as well as a site that stands out from the typical MSP site.

We would like to maintain our current site in order to retain SEO, update the technology used (current site is flash based), mobile (Zelphone, Zelpad, Orbitel Phone) compatible and Color Theme update (likely orange and white).

My current site:
http://www.harborsystems-example.net

My chief local competition (who we want to look better than):
http://www.quillbyte-example.com/

Other MSP sites (people we want to stand out from):
http://www.lanternops-example.com/
http://www.fernacle-example.com/
Updates

Please send your email to mpatterly@harborsys-example.com if you are interested in this project so I can send you a filecrate link to the existing site files for you to work with.

https://www.filecrate-example.com/sh/4k2pq8wzrbn51tx/QQL9MvaHsT2ZwpeuNoXKA74b

We would like to have a Call to action form on the main page and an informational Video. In addition we would like the following Categories and coorisponding Icons on the Main Page. We will also need a page for each Sub-Category. The Tag line on the Landing Page / Banner should read "Enterprise Solutions for Everyone" Managed IT >Law Firms .>Associations / Nonprofits > Financial Services > Healthcare >Education Cloud Services >Server > Desktop >Managed Wireless > Voice > Restaurant Point of Sale >Pellmark Suite 365 Migrations Data Center > Managed Servers > Managed Desktops >Disaster Recovery Hosting Professional Services >Virtualization >Backup & DR Planning >Corvane Links >Mobile or Virtual Office Solutions

Target Market(s)

Small and medium business that want to have the best possible IT support.

Industry/Entity Type

Marketing

Colors
f37022

Requirements
Must have
• Convert Site from Flash to Latest web design technology i.e. DHTML. Site must be mobile friendly. Convert all Ridgeline Computing Logo Marks to Harbor Systems Logo. Change Color Theme to match uploaded files.

```html
<!DOCTYPE html>
<html lang="en">
<head>
<meta charset="utf-8">
<title>Harbor Systems – Managed IT Overview</title>
<link rel="stylesheet" href="https://fonts.googleapis.com/css2?family=Lato:ital,wght@0,300;0,400;0,700;0,900;1,400&family=Oswald:wght@400;500&display=swap">
<style>
:root{
  --orange:#f37022;
  --black:#111111;
  --ink:#3a3a3a;
  --text:#222222;
  --panel-grey:#a7a9ac;
  --band-grey:#d1d3d4;
  --benefit-grey:#c3c5c7;
  --footer:#3a3b3c;
  --art-red:#c9302a;
  --art-grey:#e4e4e4;
  --white:#ffffff;
}
*{box-sizing:border-box;margin:0;padding:0}
html,body{width:1200px;height:3310px;overflow:hidden}
body{font-family:'Lato',Arial,sans-serif;color:var(--text);background:var(--white);position:relative}
a{color:inherit;text-decoration:none}

.utility-bar{height:28px;background:var(--black);display:flex;justify-content:flex-end;align-items:center;padding-right:22px;gap:10px;font:700 13px 'Lato',sans-serif;color:var(--white)}
.utility-bar .sep{color:#777}
.utility-bar .muted{font-weight:400}

.site-header{height:138px;position:relative}
.brand{position:absolute;left:30px;top:14px;width:330px}
.brand-name{display:flex;align-items:center;gap:10px;white-space:nowrap;font:700 26px/1 'Lato',sans-serif;color:var(--ink)}
.brand-mark{width:24px;height:24px;background:var(--orange)}
.brand-art{margin-top:12px;width:290px;height:36px;background:var(--art-red)}
.brand-tagline{margin-top:8px;font:italic 400 13px 'Lato',sans-serif;color:#555;white-space:nowrap}
.social{position:absolute;right:20px;top:30px;display:flex;gap:16px}
.social span{width:34px;height:34px;border-radius:50%;background:var(--orange)}
.call{position:absolute;right:22px;top:88px;font:500 22px 'Oswald',sans-serif;color:var(--black);letter-spacing:.5px}
.call b{font-weight:500;margin-left:18px}

.main-nav{height:74px;background:var(--orange);display:flex;align-items:center;padding-left:16px;font:400 23px 'Oswald',sans-serif;color:var(--white);text-transform:uppercase;white-space:nowrap}
.main-nav a{padding:0 20px;height:74px;line-height:74px}
.main-nav a.active{background:var(--black)}

.overview{height:422px;position:relative}
.overview-title{position:absolute;left:30px;top:26px;font:300 57px 'Lato',sans-serif;color:var(--ink);white-space:nowrap}
.overview-title em{font-style:normal;color:var(--orange)}
.overview-lead{position:absolute;left:30px;top:118px;width:760px;font:400 20px/1.35 'Lato',sans-serif;color:#333}
.overview-art{position:absolute;left:30px;top:200px;width:340px;height:200px;background:var(--art-grey)}
.services-panel{position:absolute;right:0;top:0;width:386px;height:422px;background:var(--panel-grey);padding:34px 40px}
.services-panel h2{font:400 38px 'Lato',sans-serif;color:var(--black);letter-spacing:.5px}
.services-panel ul{list-style:none;margin-top:58px;max-width:280px;font:400 20px/22px 'Lato',sans-serif;color:#333;text-transform:uppercase}

.band{text-align:center;position:relative}
.band-grey{background:var(--band-grey)}
.band h2{font:300 58px/1.18 'Lato',sans-serif;color:#444}
.band .kicker{font:italic 400 21px 'Lato',sans-serif;color:var(--orange);margin-top:2px}
.band p{font:400 14px/1.45 'Lato',sans-serif;color:#222;width:940px;margin:0 auto}
.protection{height:538px;padding-top:76px}
.protection .copy{margin-top:50px}
.protection p+p{margin-top:4px}
.protection p.quote{font-weight:700;margin-top:18px}
.monitoring{height:543px;padding-top:78px}
.monitoring .copy{margin-top:52px}

.benefits{height:541px;background:var(--band-grey);position:relative}
.benefits-body{position:absolute;left:0;top:150px;width:840px;text-align:center}
.benefits-body h2{font:300 58px 'Lato',sans-serif;color:#444}
.benefits-body .kicker{font:italic 400 21px 'Lato',sans-serif;color:var(--orange)}
.benefits-body p{width:780px;margin:44px auto 0;font:400 14px/1.45 'Lato',sans-serif;color:#222}
.benefits-panel{position:absolute;right:0;top:0;width:350px;height:541px;background:var(--benefit-grey);padding:36px 24px}
.benefits-panel h3{font:400 32px 'Lato',sans-serif;color:var(--black)}
.benefits-panel ul{list-style:none;margin-top:24px;font:400 13px/1.3 'Lato',sans-serif;color:#222}
.benefits-panel li{margin-bottom:18px;max-width:235px}

.supplement{height:543px;padding-top:92px}
.supplement .copy{margin-top:56px}

.site-footer{height:483px;background:var(--footer);color:var(--white);position:relative}
.footer-cols{position:absolute;left:60px;top:76px;display:flex}
.footer-col{width:216px}
.footer-col h4{font:700 18px 'Lato',sans-serif;margin-bottom:22px}
.footer-col ul{list-style:none;font:400 14px/1.15 'Lato',sans-serif}
.footer-col li.strong{font-weight:700}
.footer-col li.indent{padding-left:20px}
.footer-legal{position:absolute;left:0;right:0;top:320px;text-align:center;font:400 14px 'Lato',sans-serif}
.footer-legal span{margin:0 24px}
</style>
</head>
<body>

<div class="utility-bar">
  <a href="#">Home</a><span class="sep">|</span>
  <a href="#">Submit Trouble Ticket</a><span class="sep">|</span>
  <a href="#" class="muted">Pay Bill Online</a><span class="sep">|</span>
  <a href="#">Blog</a><span class="sep">|</span>
  <a href="#">Client Login</a>
</div>

<header class="site-header">
  <div class="brand">
    <div class="brand-name"><span class="brand-mark"></span>Harbor Systems</div>
    <div class="brand-art" role="img" aria-label="Marketing illustration of a row of fruit"></div>
    <div class="brand-tagline">We do IT our own way and we're happy about it!</div>
  </div>
  <div class="social" aria-label="Social links"><span></span><span></span><span></span></div>
  <div class="call">CALL TODAY <b>(866) 555-0142</b></div>
</header>

<nav class="main-nav">
  <a href="#">Home</a>
  <a href="#" class="active">Extraordinary Services</a>
  <a href="#">Cloud Services</a>
  <a href="#">Data Center</a>
  <a href="#">Professional Services</a>
  <a href="#">About Us</a>
</nav>

<section class="overview">
  <h1 class="overview-title"><em>Managed IT</em> Overview</h1>
  <p class="overview-lead">Harbor Systems provides extraordinary Proactive IT monitoring and support that delivers Enterprise IT capabilities to organizations of all sizes.</p>
  <div class="overview-art" role="img" aria-label="Illustration of a team of grey figures with one orange leader"></div>
  <aside class="services-panel">
    <h2>SERVICES</h2>
    <ul>
      <li>Small &amp; Mid-Size Business</li>
      <li>Law Firms</li>
      <li>Associations / Non Profits</li>
      <li>Financial Services</li>
      <li>Healthcare</li>
      <li>Education</li>
    </ul>
  </aside>
</section>

<section class="band band-grey protection">
  <h2>Harbor Systems<br>Total Protection Service Plan</h2>
  <div class="kicker">We make it easy for you to do what you do!</div>
  <div class="copy">
    <p>Harbor Systems is dedicated to keeping your technology investment up and running smoothly so you can focus on your business. You can relax knowing our partnership with your organization means we take your IT personally, and strive to keep your staff productive with the tools they need to drive our business forward.</p>
    <p>Change the way you think about IT with Harbor Systems. Think of us as your one stop shop for all your technology needs. We strategically optimize and protect your infrastructure while performing day - to - day maintenance that keeps your users from experiencing downtime.</p>
    <p class="quote">"Why settle for that IT guy who is sometimes available and only shows up when something is broken.You can have an entire enterprise support department at your disposal."</p>
  </div>
</section>

<section class="band monitoring">
  <h2>24x7x365 Proactive Monitoring and<br>Maintenance</h2>
  <div class="kicker">Detect and stop IT issues before they affect your bottom line</div>
  <div class="copy">
    <p>Harbor Systems' IT Services are built to cover all of your IT support needs, from your employee workstations to your servers, and even other devices on your network that are necessary for your organization's efficiency. By performing regular maintenance and monitoring your systems 24x7x365, we can drastically reduce the amount of downtime your staff experience.<br>Our team is always looking out for your business and your goals, and can help you meet your IT needs as you expand. Our proactive maintenance can keep your IT investments running smoothly and our experienced support staff can assist your users with any technology -related issues.</p>
  </div>
</section>

<section class="benefits">
  <div class="benefits-body">
    <h2>The Benefits of Flat-Rate IT</h2>
    <div class="kicker">Finally budget your IT expenses</div>
    <p>Imagine being able to finally budget your technology. Imagine how much faster issues will get resolved if your entire staff can call for support without increasing your monthly IT expenses. With Harbor Systems, you and your staff can rest assured that you can focus entirely on other business issues that need your attention, not your IT. In the long run, you save money with fewer issues, less downtime, and a no - surprises flat - rate that's designed to work for small businesses.</p>
  </div>
  <aside class="benefits-panel">
    <h3>BENEFITS</h3>
    <ul>
      <li>Slash the cost of IT</li>
      <li>Proactive 24x7 monitoring and protection</li>
      <li>Flat-Rate IT is easy to budget and we provide an updated 3-year IT budget every quarter</li>
      <li>Reduce and prevent downtime across your entire infrastructure 24x7x365 System Monitoring and maintenance</li>
      <li>Quarterly Technology Assessment Detailed Quarterly review and re-porting</li>
      <li>Worry free backup and protection Your infrastructure is thoroughly documented at all times</li>
      <li>Enterprise level care</li>
    </ul>
  </aside>
</section>

<section class="band supplement">
  <h2>Supplement Your Current<br>Internal IT</h2>
  <div class="kicker">Benefit from Harbor Systems 's Flexibility</div>
  <div class="copy">
    <p>Already have an internal IT department or a technical guru on site that handles most of your day - to - day IT issues? Harbor Systems isn't out to replace them, but we can certainly supplement and assist your current internal IT staff providing our 24x7x365 monitoring, maintenance, and support. Your current IT staff will be able to take advantage of us as we strive to prevent downtime. If your current IT department is overloaded, Harbor Systems is the perfect solution for lightening their workload to ensure the rest of your company co tinues to function without a hitch.</p>
  </div>
</section>

<footer class="site-footer">
  <div class="footer-cols">
    <div class="footer-col">
      <h4>Top Level Services</h4>
      <ul>
        <li>Managed IT</li>
        <li class="strong">Small &amp; Mid-Size Businesses</li>
        <li>Law Firms</li>
        <li>Associations / Non-Profits</li>
        <li>Financial Services</li>
        <li>Healthcare</li>
        <li>Education</li>
      </ul>
    </div>
    <div class="footer-col">
      <h4>Cloud Services</h4>
      <ul>
        <li>Backup &amp; Disaster Recovery</li>
        <li>Public &amp; Private Cloud Server</li>
        <li>Solutions</li>
        <li>Voice</li>
        <li>Pellmark Suite 365 Migrations</li>
        <li>Restaurant Point of Sale</li>
      </ul>
    </div>
    <div class="footer-col">
      <h4>Data Center</h4>
      <ul>
        <li>Managed Servers</li>
        <li>DR Hosting</li>
        <li>Virtual Office Solutions</li>
      </ul>
    </div>
    <div class="footer-col">
      <h4>Professional Services</h4>
      <ul>
        <li>Virtualization</li>
        <li>Corvane Links</li>
        <li>Virtual Office Design &amp;</li>
        <li class="indent">Deployment</li>
        <li>Restaurant POS Design &amp;</li>
        <li class="indent">Deployment</li>
      </ul>
    </div>
    <div class="footer-col">
      <h4>About Us</h4>
      <ul>
        <li>Who we are</li>
        <li>Testimonials</li>
        <li>Partners</li>
        <li>Locations</li>
        <li>Site</li>
      </ul>
    </div>
  </div>
  <div class="footer-legal">
    <a href="#">franchise opportunites</a><span>|</span><a href="#">terms</a><span>|</span><a href="#">privacy policy</a>
  </div>
</footer>

</body>
</html>
```